Quill Thistle Co. needs a new Label for our bottle!

We need a creative label for our 8oz bottle of Quill Thistle Odor Eliminator concentrate. (see attachment for Label specifications). The winner of this contest will probably be used to complete the other products bottle labels we will be launching in the next few months as all of our labels will be similar to this design.
Updates

Project Deadline Extended
Reason: We have extended the contest 5 days. Please submit final designs. Thank you

Target Market(s)

Customers who are trying to get rid of an odor in their house or business

Industry/Entity Type

Cleaning Product

Colors

Designer to choose colors to be used in the design.

Requirements
Must have
• - A lemon on the front of the label that stands out so when people are scrolling product listings on tradivo that they stop on our listing.
• - Vintage old-fashioned look to label
• (Update 10/22) - The label will on a 8oz round amber bottle (see bottle picture at https://www.crateandvesselsupply.com/item/B292)
• (Update 10/22) - The website address "www.quillthistleco.com" should be on back of label.
• (Update 10/22) - "Feedback or Questions? Please email customer@quillthistleco.com"
• (see attachment for Label specifications)
Nice to have
Should not have

```html
<!DOCTYPE html>
<html lang="en">
<head>
<meta charset="utf-8">
<title>Quill Thistle Co. Odor Eliminator Label</title>
<link rel="stylesheet" href="https://fonts.googleapis.com/css2?family=Oswald:wght@500;600;700&family=Roboto+Condensed:wght@700&display=swap">
<style>
  :root {
    --page-bg: #f4f1ec;
    --label-top: #f9c21f;
    --label-mid: #f6a523;
    --label-bottom: #f08a26;
    --band: #e9772b;
    --band-edge: #d9661f;
    --ink-light: #ffffff;
    --lemon-rind: #f3e23a;
    --lemon-flesh: #e2e07a;
    --leaf: #4f9a3a;
  }
  html, body {
    margin: 0;
    padding: 0;
    width: 900px;
    height: 1200px;
    overflow: hidden;
    background: var(--page-bg);
  }
  .label {
    position: absolute;
    left: 70px;
    top: 60px;
    width: 760px;
    height: 1080px;
    background: linear-gradient(180deg, var(--label-top) 0%, var(--label-mid) 55%, var(--label-bottom) 100%);
    overflow: hidden;
  }
  .brand {
    position: absolute;
    top: 150px;
    left: 0;
    width: 100%;
    text-align: center;
    margin: 0;
    font-family: "Oswald", sans-serif;
    font-weight: 700;
    font-size: 118px;
    line-height: 1;
    letter-spacing: -1px;
    color: var(--ink-light);
    text-transform: uppercase;
  }
  .hero-art {
    position: absolute;
    left: 150px;
    top: 380px;
    width: 500px;
    height: 390px;
  }
  .product-band {
    position: absolute;
    left: 0;
    top: 770px;
    width: 100%;
    height: 190px;
    background: var(--band);
    border-top: 2px solid var(--band-edge);
    border-bottom: 2px solid var(--band-edge);
    text-align: center;
    color: var(--ink-light);
  }
  .product-name {
    margin: 22px 0 0;
    font-family: "Oswald", sans-serif;
    font-weight: 600;
    font-size: 66px;
    line-height: 1;
    letter-spacing: 2px;
    word-spacing: 14px;
  }
  .uses {
    margin: 20px auto 0;
    width: 640px;
    font-family: "Roboto Condensed", sans-serif;
    font-weight: 700;
    font-size: 25px;
    line-height: 1.3;
  }
  .volume {
    position: absolute;
    top: 1000px;
    left: 0;
    width: 100%;
    text-align: center;
    margin: 0;
    font-family: "Oswald", sans-serif;
    font-weight: 500;
    font-size: 48px;
    color: var(--ink-light);
    letter-spacing: 1px;
  }
</style>
</head>
<body>
  <main class="label">
    <h1 class="brand">Quill Thistle Co.</h1>

    <svg class="hero-art" viewBox="0 0 500 390" role="img" aria-label="Photograph of a halved lemon with green leaves">
      <defs>
        <radialGradient id="lemonTone" cx="45%" cy="45%" r="55%">
          <stop offset="0%" stop-color="var(--lemon-flesh)"/>
          <stop offset="85%" stop-color="var(--lemon-flesh)"/>
          <stop offset="100%" stop-color="var(--lemon-rind)"/>
        </radialGradient>
        <linearGradient id="leafTone" x1="0" y1="0" x2="1" y2="1">
          <stop offset="0%" stop-color="#6bb04c"/>
          <stop offset="100%" stop-color="var(--leaf)"/>
        </linearGradient>
      </defs>
      <circle cx="215" cy="195" r="185" fill="url(#lemonTone)"/>
      <rect x="300" y="150" width="200" height="240" rx="90" fill="url(#leafTone)"/>
    </svg>

    <section class="product-band">
      <h2 class="product-name">ODOR ELIMINATOR</h2>
      <p class="uses">Pet Odors, Pet Urine, Carpet, Wood Floors,<br>Litter Boxes, Basements, Trash Containers.</p>
    </section>

    <p class="volume">8 FL OZ(237 ML)</p>
  </main>
</body>
</html>
```